ember-ridge builders and works

I need a web design for my company we offer counter tops. tile for floors,showers,kitchen backsplashes and more also need a place where the client
can write reviews

Tile

```html
<!DOCTYPE html>
<html lang="en">
<head>
<meta charset="utf-8">
<title>Ember Ridge — Counter Tops &amp; Tile</title>
<link rel="stylesheet" href="https://fonts.googleapis.com/css2?family=Cinzel:wght@400;700&family=Open+Sans:wght@400;600;700&family=Noto+Serif&family=Oswald:wght@300&display=swap">
<style>
:root{
  --red:#8b0000;
  --dark:#262b36;
  --peach:#f4cba3;
  --peach-text:#7a3512;
  --light:#eef0f4;
  --white:#ffffff;
  --grey-text:#4b4f5a;
  --line:#8e929b;
}
*{margin:0;padding:0;box-sizing:border-box}
html,body{width:718px;height:1200px;overflow:hidden}
body{position:relative;background:var(--dark);font-family:"Open Sans",Arial,sans-serif;color:var(--white)}
h2,h3{font-weight:400}
.abs{position:absolute}
.top-strip{left:0;top:0;width:718px;height:11px;background:var(--red)}
.header{left:0;top:11px;width:718px;height:87px;background:var(--dark)}
.brand{left:203px;top:22px;width:336px;height:34px;border-top:1px solid #8c909a;border-bottom:1px solid #8c909a;text-align:center;font-family:"Cinzel",serif;font-size:25px;line-height:33px;color:var(--white)}
.nav{left:203px;top:67px;width:336px;text-align:center;font-family:"Cinzel",serif;font-size:10px;letter-spacing:.3px;white-space:nowrap}
.nav span{margin:0 6px}
.nav .dot{margin:0 4px}
.hero{left:0;top:98px;width:718px;height:362px;background:linear-gradient(180deg,#3a2a24 0%,#6b5a4c 35%,#d9cbb6 60%,#efe3cf 78%,#b9a88e 100%)}
.featured-panel{left:16px;top:410px;width:688px;height:342px;background:var(--red)}
.promo{left:24px;top:426px;width:674px;height:76px;background:var(--peach);border:1px solid #e5b58b;text-align:center}
.promo-title{font-family:"Cinzel",serif;font-size:16px;color:var(--peach-text);margin-top:14px;letter-spacing:.3px}
.promo-rule{width:310px;height:1px;background:#d9a47a;margin:5px auto 4px}
.promo-sub{font-size:10px;color:#b1673a}
.section-title{font-family:"Cinzel",serif;font-size:14px;letter-spacing:.2px}
.featured-title{left:32px;top:523px;color:var(--peach)}
.featured-rule{left:32px;top:545px;width:666px;height:1px;background:#a83a2a}
.arrows{left:644px;top:525px}
.product{width:138px}
.product-photo{width:138px;height:131px;border:1px solid #c0392b;background:linear-gradient(160deg,#5a3a28,#b99472 55%,#e6d5bd)}
.product-name{margin-top:10px;font-size:9px;font-weight:700;color:var(--white);line-height:12px}
.product-desc{margin-top:1px;font-family:"Noto Serif",serif;font-size:9.5px;line-height:13px;color:var(--peach);white-space:nowrap}
.product-price{margin-top:1px;font-family:"Oswald",sans-serif;font-weight:300;font-size:18px;line-height:24px;letter-spacing:-.5px;color:var(--peach)}
.testimonials{left:0;top:766px;width:718px;height:198px;background:var(--light)}
.testimonials-title{left:26px;top:778px;font-size:17px;color:#4a4f5c}
.testimonials-rule{left:21px;top:802px;width:669px;height:1px;background:var(--line)}
.avatar{width:36px;height:46px;border:1px solid #9aa0a8;background:linear-gradient(180deg,#6a5a50,#c9a88d)}
.bubble{width:141px;height:89px;border:1px solid #9aa0a8;background:var(--light);padding:7px 6px 7px 8px;font-family:Arial,sans-serif;font-size:8.5px;line-height:10.6px;color:#5c6170}
.bubble::before{content:"";position:absolute;left:-10px;top:12px;border:4px solid transparent;border-right:5px solid #9aa0a8}
.reviewer{font-family:Arial,sans-serif;font-size:10.5px;font-weight:700;color:var(--red)}
.reviewer-role{font-family:Arial,sans-serif;font-size:8.5px;color:#5c6170}
.footer-col{width:208px}
.footer-heading{border-top:1px solid #6c707a;border-bottom:1px solid #6c707a;height:23px;font-family:"Cinzel",serif;font-size:17px;line-height:23px;padding-left:1px}
.footer-about{margin-top:16px;font-size:8.5px;line-height:10.6px;color:#cfd2d8}
.footer-links a{position:absolute;font-size:7.5px;font-weight:700;color:var(--white);text-decoration:none;white-space:nowrap}
.copyright-bar{left:0;top:1146px;width:718px;height:41px;background:var(--red)}
.copyright{left:15px;top:1162px;font-size:8px;color:var(--white)}
</style>
</head>
<body>
<div class="abs top-strip"></div>
<header class="abs header"></header>
<div class="abs brand">EMBER RIDGE</div>
<nav class="abs nav"><span>HOME</span><span class="dot">·</span><span>ABOUT US</span><span class="dot">·</span><span>PRODUCTS</span><span class="dot">·</span><span>CONTACT US</span></nav>

<div class="abs hero" role="img" aria-label="Bright kitchen with a light stone island counter, steel sink and faucet, dark cabinets and a tiled backsplash"></div>

<section class="abs featured-panel"></section>
<div class="abs promo">
  <div class="promo-title">FREE SHIPPING ON ALL ORDERS OVER $150</div>
  <div class="promo-rule"></div>
  <div class="promo-sub">NO REQUIREMENTS REQUIRED JUST SHOP ABOVE $150</div>
</div>
<h2 class="abs section-title featured-title">FEATURED PRODUCTS</h2>
<div class="abs featured-rule"></div>
<svg class="abs arrows" width="36" height="14" viewBox="0 0 36 14" aria-label="Previous and next">
  <polygon points="12,1 12,13 2,7" fill="var(--peach)"/>
  <polygon points="24,1 24,13 34,7" fill="var(--peach)"/>
</svg>

<div class="abs product" style="left:32px;top:554px">
  <div class="product-photo" role="img" aria-label="Kitchen island with speckled granite counter top"></div>
  <div class="product-name">PRODUCT NAME</div>
  <div class="product-desc">Ridge 89 Quarry Slab Top</div>
  <div class="product-price">$101.23</div>
</div>
<div class="abs product" style="left:201px;top:554px">
  <div class="product-photo" role="img" aria-label="Curved gold toned granite counter beside a column"></div>
  <div class="product-name">PRODUCT NAME</div>
  <div class="product-desc">Ridge 89 Quarry Slab Top</div>
  <div class="product-price">$101.23</div>
</div>
<div class="abs product" style="left:370px;top:554px">
  <div class="product-photo" style="background:linear-gradient(160deg,#6b5a48,#2c2f30 55%,#7a5a3a)" role="img" aria-label="Dark curved granite bar counter"></div>
  <div class="product-name">PRODUCT NAME</div>
  <div class="product-desc">Ridge 89 Quarry Slab Top</div>
  <div class="product-price">$101.23</div>
</div>
<div class="abs product" style="left:538px;top:554px">
  <div class="product-photo" style="background:linear-gradient(160deg,#b06a4a,#e8e6e2 50%,#6a2e1c)" role="img" aria-label="White quartz counter with wood cabinets"></div>
  <div class="product-name">PRODUCT NAME</div>
  <div class="product-desc">Ridge 89 Quarry Slab Top</div>
  <div class="product-price">$101.23</div>
</div>

<section class="abs testimonials"></section>
<h2 class="abs section-title testimonials-title">TESTIMONIALS</h2>
<div class="abs testimonials-rule"></div>

<div class="abs avatar" style="left:20px;top:826px" role="img" aria-label="Reviewer portrait"></div>
<div class="abs bubble" style="left:71px;top:826px">Ut enim ad minim veniam, quis nostrud exercitation ullamco laboris nisi ut aliquip ex ea commodo consequat. Duis aute irure dolor in reprehenderit in voluptate velit esse cillum dolore eu fugiat nulla pariatur.</div>
<div class="abs" style="left:70px;top:923px"><div class="reviewer">Ravi Tolman</div><div class="reviewer-role">Real Estate Guru</div></div>

<div class="abs avatar" style="left:260px;top:826px" role="img" aria-label="Reviewer portrait"></div>
<div class="abs bubble" style="left:310px;top:826px">Ut enim ad minim veniam, quis nostrud exercitation ullamco laboris nisi ut aliquip ex ea commodo consequat. Duis aute irure dolor in reprehenderit in voluptate velit esse cillum dolore eu fugiat nulla pariatur.</div>
<div class="abs" style="left:309px;top:923px"><div class="reviewer">Lena Marcott</div><div class="reviewer-role">Interior Designer</div></div>

<div class="abs avatar" style="left:500px;top:826px" role="img" aria-label="Reviewer portrait"></div>
<div class="abs bubble" style="left:551px;top:826px">Ut enim ad minim veniam, quis nostrud exercitation ullamco laboris nisi ut aliquip ex ea commodo consequat. Duis aute irure dolor in reprehenderit in voluptate velit esse cillum dolore eu fugiat nulla pariatur.</div>
<div class="abs" style="left:550px;top:923px"><div class="reviewer">Owen Haldane</div><div class="reviewer-role">Civil Engineer</div></div>

<footer>
  <div class="abs footer-col" style="left:11px;top:984px">
    <h3 class="footer-heading">ABOUT US</h3>
    <p class="footer-about">Lorem ipsum dolor sit amet, consectetur adipisicing elit, sed do eiusmod tempor incididunt ut labore et dolore magna aliqua. Ut enim ad minim veniam, quis nostrud exercitation ullamco laboris nisi ut aliquip ex ea commodo consequat.</p>
  </div>
  <div class="abs footer-col" style="left:257px;top:984px">
    <h3 class="footer-heading">INFORMATION</h3>
    <div class="footer-links">
      <a style="left:2px;top:34px">TRACK ORDERS</a><a style="left:127px;top:34px">BLOG</a>
      <a style="left:2px;top:55px">FAQS</a><a style="left:127px;top:55px">ABOUT US</a>
      <a style="left:2px;top:75px">PORTFOLIO</a><a style="left:127px;top:75px">SERVICES</a>
      <a style="left:2px;top:96px">SHOP SALES</a><a style="left:127px;top:96px">CONTACT US</a>
    </div>
  </div>
  <div class="abs footer-col" style="left:497px;top:984px;width:209px">
    <h3 class="footer-heading">CONNECT</h3>
  </div>
  <svg class="abs" style="left:496px;top:1016px" width="154" height="28" viewBox="0 0 154 28" aria-label="Social links">
    <circle cx="14" cy="14" r="13" fill="var(--white)"/>
    <circle cx="45.5" cy="14" r="13" fill="var(--white)"/>
    <circle cx="77" cy="14" r="13" fill="var(--white)"/>
    <circle cx="108.5" cy="14" r="13" fill="var(--white)"/>
    <circle cx="140" cy="14" r="13" fill="var(--white)"/>
  </svg>
</footer>

<div class="abs copyright-bar"></div>
<p class="abs copyright">© Copyright Ember Ridge 2014. All Rights Reserved</p>
</body>
</html>
```